Torvane Email Signature Banners – Fabrication Capability Series

www.Torvane.com.au is an Australian engineering and fabrication company specialising in fabrication and welding of :
steel piping spools,
skids and frames,
small volume process steel tanks
and general steel fabrication
We require four distinct banner designs for use in Microsoft Lintaro email signatures. Each banner will highlight a specific capability while maintaining a consistent brand identity.
Deliverables
Four banners total:
Piping Spools Fabrication – focus on precision welding and stainless steel pipework
Skid & Frames Fabrication – highlight skid systems and structural frames
Small Steel Tanks Fabrication – show fabricated tanks and workshop craftsmanship
General Fabrication Solutions – broad steel fabrication theme for company-wide use
Dimensions: 600–700 px wide × 100 px high
Format: PNG (preferred), small file size prefered
Resolution: 72 dpi
Background: non-transparent, industrial or workshop setting
Text examples:
1. Piping Spools Fabrication
Option A: “Expert Fabrication Solutions for Process Piping”
Option B: “Precision Welding for Complex Systems”
Option C: “Delivering Quality in Every Spool”
Option D: “Engineered for Flow, Built for Strength”
2. Skid & Frames Fabrication
Option A: “Custom Engineered Modular Systems”
Option B: “Built Strong. Designed Smart.”
Option C: “Reliable Frames for Industrial Performance”
Option D: “Modular Fabrication for Seamless Integration”
3. Small Steel Tanks Fabrication
Option A: “Precision Built for Your Needs”
Option B: “Compact Strength. Proven Durability.”
Option C: “Fabricated for Performance and Longevity”
Option D: “Small Tanks. Big Reliability.”
4. General Fabrication Solutions
Option A: “Quality Craftsmanship, Proven Results”
Option B: “Your Partner in Precision Fabrication”
Option C: “Engineering Excellence in Every Weld”
Option D: “Australian Fabrication. Global Standards.”
Style Direction
Clean, professional, and engineering‑focused
Use Torvane brand colours
Blend photo realism with vector clarity (no heavy gradients)
Include subtle industrial textures or workshop imagery
Typography: bold sans‑serif, legible at small scale
Usage Context
These banners will appear at the bottom of staff email signatures via Lintaro Email Signature Tool for Microsoft 365, so clarity and fast loading are essential. No Logo is required in the banners.
Reference
Existing Torvane signature is attached. Colour palette to match the signature style and logo.
Target Market(s)
Engineering and construction companies,
Industry/Entity Type
Engineering fabrication design
Look and feel

```html
<!DOCTYPE html>
<html lang="en">
<head>
<meta charset="utf-8">
<title>Torvane Email Signature Banners</title>
<link href="https://fonts.googleapis.com/css2?family=Poppins:ital,wght@1,400;1,700;1,800&display=swap" rel="stylesheet">
<style>
  :root {
    --page-bg: #e2e2e2;
    --banner-bg: #ffffff;
    --brand-blue: #1ea6e6;
    --ink: #1f1f1f;
    --chevron-dark: #151515;
    --photo-dark: #23262b;
    --photo-mid: #4a5058;
    --photo-spark: #8fa3b5;
  }
  * { margin: 0; padding: 0; box-sizing: border-box; }
  html, body {
    width: 1200px;
    height: 476px;
    overflow: hidden;
    background: var(--page-bg);
  }
  .canvas {
    position: relative;
    width: 1200px;
    height: 476px;
  }
  .banner {
    position: absolute;
    left: 50px;
    width: 1104px;
    height: 184px;
    background: var(--banner-bg);
    overflow: hidden;
  }
  .banner--general { top: 37px; }
  .banner--piping { top: 245px; }
  .banner__art {
    position: absolute;
    inset: 0;
    width: 1104px;
    height: 184px;
    display: block;
  }
  .banner__copy {
    position: absolute;
    top: 22px;
    font-family: "Poppins", sans-serif;
    font-style: italic;
  }
  .banner--general .banner__copy { left: 688px; }
  .banner--piping .banner__copy { left: 668px; top: 18px; }
  .banner__title {
    color: var(--brand-blue);
    font-weight: 800;
    font-size: 29px;
    line-height: 35px;
    letter-spacing: 0.3px;
    text-transform: uppercase;
  }
  .banner--piping .banner__title { font-size: 31px; line-height: 37px; letter-spacing: 1.2px; }
  .banner__tagline {
    margin-top: 8px;
    color: var(--ink);
    font-weight: 400;
    font-size: 24px;
    line-height: 33px;
  }
  .banner--piping .banner__tagline { margin-top: 4px; }
</style>
</head>
<body>
<main class="canvas">

  <section class="banner banner--general">
    <svg class="banner__art" viewBox="0 0 1104 184" xmlns="http://www.w3.org/2000/svg">
      <defs>
        <linearGradient id="welding-tone" x1="0" y1="0" x2="1" y2="1">
          <stop offset="0" stop-color="var(--photo-dark)"/>
          <stop offset="0.55" stop-color="var(--photo-mid)"/>
          <stop offset="0.75" stop-color="var(--photo-spark)"/>
          <stop offset="1" stop-color="var(--photo-dark)"/>
        </linearGradient>
      </defs>
      <g role="img" aria-label="Photo of a welder in gloves welding steel with sparks flying">
        <polygon points="100,0 600,0 505,184 0,184 0,120" fill="url(#welding-tone)"/>
      </g>
      <polygon points="622,0 676,0 580,184 526,184" fill="var(--brand-blue)"/>
      <polygon points="606,0 614,0 518,184 510,184" fill="var(--brand-blue)"/>
      <polygon points="0,70 240,184 0,184" fill="var(--brand-blue)"/>
    </svg>
    <div class="banner__copy">
      <h2 class="banner__title">General Fabrication<br>Solutions</h2>
      <p class="banner__tagline">Quality Craftsmanship,<br>Proven Results</p>
    </div>
  </section>

  <section class="banner banner--piping">
    <svg class="banner__art" viewBox="0 0 1104 184" xmlns="http://www.w3.org/2000/svg">
      <defs>
        <linearGradient id="piping-tone" x1="0" y1="0" x2="1" y2="1">
          <stop offset="0" stop-color="var(--photo-dark)"/>
          <stop offset="0.45" stop-color="var(--photo-mid)"/>
          <stop offset="0.7" stop-color="var(--photo-spark)"/>
          <stop offset="1" stop-color="var(--photo-dark)"/>
        </linearGradient>
      </defs>
      <g role="img" aria-label="Photo of a gloved welder TIG welding stainless steel pipe spools">
        <polygon points="0,0 436,0 482,92 436,184 0,184" fill="url(#piping-tone)"/>
      </g>
      <polyline points="452,0 498,92 452,184" fill="none" stroke="var(--brand-blue)" stroke-width="6"/>
      <polyline points="504,28 536,92 504,156" fill="none" stroke="var(--chevron-dark)" stroke-width="6"/>
      <polygon points="524,30 548,30 580,92 548,154 524,154 556,92" fill="var(--brand-blue)"/>
      <polygon points="566,30 590,30 622,92 590,154 566,154 598,92" fill="var(--brand-blue)"/>
    </svg>
    <div class="banner__copy">
      <h2 class="banner__title">Piping Spools<br>Fabrication</h2>
      <p class="banner__tagline">Expert Fabrication Solutions<br>for Process Piping</p>
    </div>
  </section>

</main>
</body>
</html>
```